Spring Detox sale graphics for social media

You MUST read the Brief in the WORD document and follow the instructions there. I want to create 10 social media graphics (new Instagram size 4:5 (1080 x 1350 pixels) focusing on our Mother’s Day Spring Detox Sale graphics, using any of the pics attached. Use the attached pics, NO RANDOM STOCK PHOTOGRAPHY. For the color scheme of the graphics, they should all be complementary to the product colors or feel like Spring time.

Target Market(s)

primarily women

Requirements
Must have
• the photos and text attached

```html
<!DOCTYPE html>
<html lang="en">
<head>
<meta charset="utf-8">
<title>Mother's Day Spring Detox Sale</title>
<link href="https://fonts.googleapis.com/css2?family=Italiana&family=Montserrat:wght@700;800&display=swap" rel="stylesheet">
<style>
  :root {
    --spring-green: #a9bb64;
    --line-green: #bccb84;
    --dot-green: #c2d08e;
    --blossom-pink: #d9657f;
    --white: #ffffff;
    --petal-blush: #f6dfe0;
    --sun-yellow: #f7cf4a;
    --stem-green: #6f8a3a;
  }
  html, body {
    margin: 0;
    padding: 0;
    overflow: hidden;
  }
  p, h1 { margin: 0; }
  .canvas {
    position: relative;
    width: 960px;
    height: 1200px;
    background: var(--spring-green);
    overflow: hidden;
    font-family: "Montserrat", Arial, sans-serif;
    color: var(--white);
  }
  .backdrop-curves {
    position: absolute;
    inset: 0;
    width: 960px;
    height: 1200px;
  }
  .eyebrow {
    position: absolute;
    top: 64px;
    left: 0;
    width: 100%;
    text-align: center;
    font-family: "Italiana", Georgia, serif;
    font-size: 66px;
    line-height: 1;
  }
  .headline {
    position: absolute;
    left: 0;
    width: 100%;
    text-align: center;
    font-weight: 800;
    line-height: 1;
  }
  .headline--spring { top: 139px; font-size: 150px; letter-spacing: 1px; }
  .headline--detox  { top: 269px; font-size: 150px; letter-spacing: 1px; }
  .sale-band {
    position: absolute;
    left: 180px;
    top: 431px;
    width: 600px;
    height: 107px;
    background: var(--blossom-pink);
    display: flex;
    align-items: center;
    justify-content: center;
  }
  .sale-band__text {
    font-family: "Italiana", Georgia, serif;
    font-size: 112px;
    line-height: 1;
    margin-top: -12px;
  }
  .offer {
    position: absolute;
    top: 548px;
    left: 0;
    width: 100%;
    text-align: center;
    font-weight: 800;
    font-size: 136px;
    line-height: 1;
  }
  .everything-band {
    position: absolute;
    left: 0;
    top: 702px;
    width: 960px;
    height: 78px;
    background: var(--white);
    display: flex;
    align-items: center;
    justify-content: center;
  }
  .everything-band__text {
    color: var(--spring-green);
    font-weight: 700;
    font-size: 58px;
    letter-spacing: 16px;
    margin-left: 16px;
    line-height: 1;
  }
  .art { position: absolute; }
  .art--leaves {
    right: 0;
    top: 0;
    width: 160px;
    height: 160px;
    background: linear-gradient(200deg, var(--petal-blush), rgba(255,255,255,0.5));
    border-bottom-left-radius: 120px;
    opacity: 0.85;
  }
  .art--daisies {
    left: 8px;
    top: 792px;
    width: 312px;
    height: 408px;
    background: linear-gradient(180deg, var(--sun-yellow) 0%, #c6c25a 45%, var(--stem-green) 100%);
    border-top-left-radius: 140px;
    border-top-right-radius: 140px;
    opacity: 0.55;
  }
  .art--bottles {
    left: 222px;
    top: 813px;
    width: 627px;
    height: 369px;
    background: linear-gradient(180deg, #fbfbfb 0%, #f1eff1 70%, #ece4ea 100%);
    border-radius: 24px 24px 10px 10px;
  }
</style>
</head>
<body>
  <main class="canvas">
    <svg class="backdrop-curves" viewBox="0 0 960 1200" aria-hidden="true">
      <g fill="none" stroke="var(--line-green)" stroke-width="2">
        <path d="M 0 360 C 120 250 260 300 340 210 C 400 140 380 60 300 30"/>
        <path d="M 90 0 C 140 80 250 110 360 80"/>
        <path d="M 0 690 C 60 560 120 470 40 380"/>
        <path d="M 960 520 C 900 600 860 700 900 780"/>
        <path d="M 840 860 C 900 900 940 980 960 1040"/>
        <path d="M 600 1200 C 680 1120 820 1110 960 1150"/>
      </g>
      <g fill="var(--dot-green)">
        <circle cx="879" cy="355" r="9"/>
        <circle cx="837" cy="400" r="8"/>
        <circle cx="889" cy="405" r="9"/>
        <circle cx="395" cy="802" r="11"/>
      </g>
    </svg>

    <div class="art art--leaves" role="img" aria-label="Pale pink and white spring leaf sprig in the corner"></div>

    <p class="eyebrow">Mother's Day</p>
    <h1 class="headline headline--spring">SPRING</h1>
    <h1 class="headline headline--detox">DETOX</h1>

    <div class="sale-band"><span class="sale-band__text">sale</span></div>

    <p class="offer">20% OFF</p>

    <div class="everything-band"><span class="everything-band__text">EVERYTHING!</span></div>

    <div class="art art--daisies" role="img" aria-label="Two yellow daisies on green stems"></div>
    <div class="art art--bottles" role="img" aria-label="Four white supplement bottles with blue, green, red and pink labels"></div>
  </main>
</body>
</html>
```